Business card design for a dynamic IT consulting company

We need a business card design for a young firm, specialized in the Telecommunications/Consulting industry. The name of the company is Quindor and Partners Business Consulting Ltd. (Short name: Quindor and Partnes)
Quindor = solve read reverse, so we aim to be uncomplicated and solution-oriented. The small pipe in our logo is also related to the word solve. So we need a new business card design, which is simple, eye catching and something non traditional (I would probably prefer a square shaped design rather than a rectangle, but open for suggestions). Attached our logo.

Target Market(s)

Usually our customers are Tier1 Telecoms providers (Q-Netra, Palorix, etc) and their executives.

Industry/Entity Type

Business

Contact Information for Business Card

Name: Bence Tolnavari
Email: b.tolnavari@quindor.hu
Web: www.quindor.hu
Mobile: +36 30 518 2769
Title: Managing Director

Optional:
Company name: Quindor and Partners Ltd.
Address: 1087 Budapest, Tolvenka str. 28/C, Hungary

Font styles to use
Other font styles liked:
• helveticaneue_medium, Prime Regular are used now.

Colors

Designer to choose colors to be used in the design.

Requirements
Must have
• I would like to have a 2 sided design.
Nice to have
• I thought if we make the logo a bit bigger (without the company name), that could go to the back with the company name below. I though, if the pipe in the logo is somehow touchable on the business card, would be nice and unique.

```html
<!DOCTYPE html>
<html lang="en">
<head>
<meta charset="utf-8">
<title>Quindor and Partners – Business Card</title>
<link rel="stylesheet" href="https://fonts.googleapis.com/css2?family=Arimo:wght@400;700&display=swap">
<style>
  :root {
    --backdrop: #2b2b2b;
    --card: #f3f3f3;
    --ink: #4a4a4a;
    --accent-blue: #1a9ad6;
    --accent-magenta: #b0267f;
    --band: #5e5e5e;
    --band-text: #ffffff;
  }
  html, body {
    margin: 0;
    width: 1200px;
    height: 960px;
    overflow: hidden;
    background: var(--backdrop);
    font-family: "Arimo", Arial, sans-serif;
  }
  .canvas {
    position: relative;
    width: 1200px;
    height: 960px;
  }
  .card {
    position: absolute;
    top: 305px;
    width: 343px;
    height: 343px;
    background: var(--card);
    box-shadow: 0 2px 6px rgba(0,0,0,0.45);
  }
  .card--front { left: 200px; }
  .card--back  { left: 651px; }

  .contact {
    position: absolute;
    left: 57px;
    top: 106px;
    color: var(--ink);
    font-variant: small-caps;
  }
  .contact__name {
    margin: 0;
    font-size: 19px;
    font-weight: 700;
    color: var(--accent-blue);
    line-height: 24px;
  }
  .contact__title {
    margin: 0 0 12px;
    font-size: 15px;
    line-height: 18px;
  }
  .contact__address {
    margin: 0;
    font-style: normal;
    font-size: 14px;
    line-height: 18px;
  }
  .contact__phone {
    font-variant: normal;
    font-size: 14px;
  }

  .brand {
    position: absolute;
    left: 0;
    right: 0;
    top: 170px;
    display: flex;
    justify-content: center;
    align-items: center;
    gap: 10px;
  }
  .brand__mark {
    width: 12px;
    height: 12px;
    background: var(--accent-blue);
  }
  .brand__name {
    font-size: 30px;
    font-weight: 400;
    color: var(--band);
    letter-spacing: 0.5px;
  }

  .web-band {
    position: absolute;
    left: 0;
    right: 0;
    top: 286px;
    height: 28px;
    background: var(--band);
    color: var(--band-text);
    font-size: 14px;
    letter-spacing: 8px;
    line-height: 28px;
    text-align: center;
  }
</style>
</head>
<body>
<main class="canvas">
  <section class="card card--front" aria-label="Card front">
    <div class="contact">
      <h1 class="contact__name">Bence Tolnavari</h1>
      <p class="contact__title">Managing Director</p>
      <address class="contact__address">
        Quindor and Partners Ltd.<br>
        1087 Budapest<br>
        Tolvenka str. 28/C, Hungary<br>
        <span class="contact__phone">+36 30 518 2769</span>
      </address>
    </div>
  </section>

  <section class="card card--back" aria-label="Card back">
    <div class="brand">
      <span class="brand__mark"></span>
      <span class="brand__name">Quindor &amp; Partners</span>
    </div>
    <div class="web-band">www.quindor.hu</div>
  </section>
</main>
</body>
</html>
```